Boutique custom software development company needs new business card

Our nearly 20 year old custom software development company would like to better include the fact that we are now providing Bitcoin services. These new services are B2B include education (how to acquire and securely hold Bitcoin) and integrating Bitcoin payments into existing ecommerce sites or other existing systems. Please keep the card clean and simple. Attached is our current design and some other files. vextorial.com

Target Market(s)

businesses owners interested in long term relationship

Industry/Entity Type

Custom software development and Bitcoin

Contact Information for Business Card

Dale Parker, dale@vextorial.com, vextorial.com, (888) 555-VXTRL

Font styles to use
Other font styles liked:
• monospace

Requirements
Must have
• double-sided
Nice to have
• clean and simple
Should not have
• physical address

```html
<!DOCTYPE html>
<html lang="en">
<head>
<meta charset="utf-8">
<title>Vextorial business card</title>
<link rel="stylesheet" href="https://fonts.googleapis.com/css2?family=Roboto+Mono:wght@400;700&family=Lato:wght@400&display=swap">
<style>
  :root {
    --page: #e8e5e0;
    --card-dark: #1b1b1c;
    --card-light: #ffffff;
    --panel-dark: #202021;
    --brand-blue: #3d70b8;
    --ink-light: #f2f2f2;
    --shadow: rgba(0, 0, 0, 0.35);
  }
  html, body {
    margin: 0;
    padding: 0;
    width: 900px;
    height: 1200px;
    overflow: hidden;
    background: var(--page);
  }
  .canvas {
    position: relative;
    width: 900px;
    height: 1200px;
  }
  .card {
    position: absolute;
    left: 78px;
    width: 744px;
    border-radius: 38px;
    box-shadow: 0 3px 8px var(--shadow);
    overflow: hidden;
  }
  .card-front {
    top: 130px;
    height: 443px;
    background: var(--card-dark);
    color: var(--ink-light);
    font-family: "Roboto Mono", monospace;
  }
  .card-back {
    top: 638px;
    height: 440px;
    background: var(--card-light);
  }
  .brand-name {
    position: absolute;
    left: 26px;
    top: 28px;
    margin: 0;
    font-family: "Roboto Mono", monospace;
    font-weight: 700;
    font-size: 60px;
    line-height: 1;
    letter-spacing: -1px;
    color: var(--brand-blue);
  }
  .tagline {
    position: absolute;
    left: 40px;
    top: 104px;
    margin: 0;
    font-family: "Lato", sans-serif;
    font-size: 22px;
    letter-spacing: -0.6px;
    color: var(--brand-blue);
  }
  .services {
    position: absolute;
    left: 26px;
    top: 200px;
    margin: 0;
    padding: 0;
    list-style: none;
    font-size: 16px;
    line-height: 24.5px;
  }
  .name-panel {
    position: absolute;
    left: 515px;
    top: 117px;
    width: 203px;
    height: 210px;
    background: var(--panel-dark);
  }
  .person {
    position: absolute;
    right: 26px;
    top: 194px;
    text-align: right;
  }
  .person-name {
    margin: 0;
    font-weight: 700;
    font-size: 28px;
    line-height: 1;
    color: var(--brand-blue);
  }
  .person-title {
    margin: 8px 0 0;
    font-size: 16px;
    line-height: 1;
  }
  .name-accent {
    position: absolute;
    right: 0;
    top: 195px;
    width: 15px;
    height: 52px;
    background: var(--brand-blue);
  }
  .contacts {
    position: absolute;
    left: 26px;
    top: 345px;
    margin: 0;
    padding: 0;
    list-style: none;
    font-size: 16px;
    line-height: 25px;
  }
  .contacts li {
    display: flex;
    align-items: center;
    gap: 7px;
  }
  .contacts svg {
    width: 18px;
    height: 16px;
    fill: var(--brand-blue);
  }
  .back-lockup {
    position: absolute;
    inset: 0;
    display: flex;
    align-items: center;
    justify-content: center;
    gap: 20px;
  }
  .back-mark {
    width: 60px;
    height: 60px;
    background: var(--brand-blue);
  }
  .back-name {
    margin: 0;
    font-family: "Roboto Mono", monospace;
    font-weight: 700;
    font-size: 56px;
    line-height: 1;
    letter-spacing: -1px;
    color: var(--brand-blue);
  }
</style>
</head>
<body>
<main class="canvas">
  <section class="card card-front" aria-label="Card front">
    <h1 class="brand-name">VEXTORIAL</h1>
    <p class="tagline">developer of custom applications</p>

    <ul class="services">
      <li>Custom software</li>
      <li>Bitcoin education &amp; custody</li>
      <li>Bitcoin payment integration</li>
    </ul>

    <div class="name-panel"></div>
    <div class="person">
      <p class="person-name">Dale Parker</p>
      <p class="person-title">Founding Partner</p>
    </div>
    <div class="name-accent"></div>

    <ul class="contacts">
      <li>
        <svg viewBox="0 0 18 16" aria-hidden="true"><path d="M2 5c0-2 3-3 7-3s7 1 7 3v1.5h-3.5V5H5.5v1.5H2z M4 8h10l1.5 6h-13z M9 9.5a2 2 0 1 0 0 4a2 2 0 1 0 0-4z"/></svg>
        <span>(888) 555-VXTRL</span>
      </li>
      <li>
        <svg viewBox="0 0 18 16" aria-hidden="true"><path d="M2 3h14v1.5L9 9 2 4.5z M2 6.3 9 10.8l7-4.5V13H2z"/></svg>
        <span>dale@vextorial.com</span>
      </li>
      <li>
        <svg viewBox="0 0 18 16" aria-hidden="true"><circle cx="9" cy="8" r="7"/><path d="M2 8h14 M9 1c-2.5 2-2.5 12 0 14 M9 1c2.5 2 2.5 12 0 14" fill="none" stroke="#1b1b1c" stroke-width="1.2"/></svg>
        <span>www.vextorial.com</span>
      </li>
    </ul>
  </section>

  <section class="card card-back" aria-label="Card back">
    <div class="back-lockup">
      <div class="back-mark"></div>
      <p class="back-name">VEXTORIAL</p>
    </div>
  </section>
</main>
</body>
</html>
```